Quirky Label Design for an Exciting UK-Based Organic Skincare Company!

We need label designs across our range of products, we are a high quality yet quirky organic skincare company called Simply Cordell, we use frosted glass packaging, and we are just wanting one design done for now, but the winning designer we would want to work with to design the rest of the labels for us. We also want them to design business cards and other literature at some point and maybe even a website page.

Our label design will go on a 63mm tall frosted glass jar which is 62mm in diameter. The actual label dimensions should be, 170 mm (W) x 50 mm (H). The idea is so that it wraps around the whole jar with the design at one side (at the front) and the ingredients on another (at the back).

LABEL 1
Organic Polynesian Whipped Body Butter
Vanilla Bean
120ml

Made with Organic Shea and Cocoa Butters and exotic Monoi de Tahiti

Ingredients (INCI): Organic Raw Shea Butter (Butyrospermum Parkii), Organic Raw Cocoa Butter (Theobroma Cacao), Monoi de Tahiti (Coconut (Cocos nucifera) oil (and) Tiare (Gardenia tahitensis) flower), Organic Sweet Almond Oil (Prunus Amygdalus Dulcis), Organic Madagascan Vanilla Extract (Vanillin)

Handmade by Simply Cordell Ltd
14 Fernwick Lane, Bournemouth BH4 9QT, UK
Batch:

OPTIONAL WRITING (if it fits in):
100% Natural and Organic
Intensely Moisturising

LABEL 2
Mango Smoothie
120ml

Ingredients (INCI): Organic Raw Shea Butter (Butyrospermum Parkii), Organic Raw Cocoa Butter (Theobroma Cacao), Monoi de Tahiti (Coconut (Cocos nucifera) oil (and) Tiare (Gardenia tahitensis) flower), Organic Sweet Almond Oil (Prunus Amygdalus Dulcis), Organic Mango Flavour (Aroma)

Batch:

100% Natural and Organic
Intensely Moisturising

I have attached a picture of the jar we use and the lid we use for these products, as well as our logo. I've also attached a 'Handmade in Dorset' stamp which we'd like to go on there if possible, along with a shelf life symbol.

I am thinking the background colour of the labels will be either white or even brown paper colour. Perhaps it would be interesting to see it in both. UPDATE: We have decided on white background now, not brown.

The final design should denote handmade, organic, high quality, pure, yet quirky and original / unique. I am thinking perhaps a seemingly hand-drawn black leaf outline? Could fit the bill, but as I say, up to you. Something that says handmade yet professional.

I'd like to have the original Photoshop files from the winning designer so we can use them as a template for the rest of our horizontal labels.
Updates

Project Deadline Extended
Reason: Just need a few more days for designs we like to be worked on further, and to review new designs!

Target Market(s)

Everyone that appreciates a good quality skincare product focusing on natural & organic. Price is mid-range to high

Industry/Entity Type

It Company

Requirements
Must have
• Must make the product look high quality & organic yet quirky and accessible. Must have our logo and the shelf life symbol and the writing as above.
Nice to have
• Nice to have the 'handmade' stamp attached, but not absolutely necessary if it doesn't fit within your design.

```html
<!DOCTYPE html>
<html lang="en">
<head>
<meta charset="utf-8">
<title>Simply Cordell – Whipped Body Butter Label</title>
<link href="https://fonts.googleapis.com/css2?family=Source+Sans+3:wght@400;600&display=swap" rel="stylesheet">
<style>
  :root {
    --canvas: #ffffff;
    --label: #eef2ef;
    --ink: #4a4340;
    --rule: #6b625e;
    --fill-warm: #efd9a6;
    --fill-soft: #ead3b8;
  }
  * { margin: 0; padding: 0; box-sizing: border-box; }
  html, body {
    width: 1200px;
    height: 1200px;
    overflow: hidden;
    background: var(--canvas);
  }
  .canvas {
    position: relative;
    width: 1200px;
    height: 1200px;
    font-family: "Source Sans 3", sans-serif;
    color: var(--ink);
  }
  .label-front {
    position: absolute;
    left: 90px;
    top: 195px;
    width: 1020px;
    height: 810px;
    background: var(--label);
  }
  .rule-top {
    position: absolute;
    left: 0;
    right: 0;
    top: 31px;
    height: 2px;
    background: var(--rule);
  }
  .brand-name {
    position: absolute;
    left: 0;
    right: 0;
    top: 120px;
    text-align: center;
    font-size: 78px;
    font-weight: 600;
    line-height: 1;
    letter-spacing: 1px;
    color: var(--ink);
  }
  .product-type {
    position: absolute;
    left: 0;
    right: 0;
    top: 340px;
    text-align: center;
    font-size: 34px;
    font-weight: 400;
    line-height: 1;
  }
  .product-rule {
    position: absolute;
    left: 158px;
    width: 715px;
    top: 392px;
    height: 2px;
    background: var(--rule);
  }
  .product-scent {
    position: absolute;
    left: 0;
    right: 0;
    top: 410px;
    text-align: center;
    font-size: 34px;
    font-weight: 400;
    line-height: 1;
  }
  .fruit-illustration {
    position: absolute;
    left: 306px;
    top: 477px;
    width: 405px;
    height: 270px;
    background: linear-gradient(135deg, var(--fill-warm), var(--fill-soft));
  }
  .volume-row {
    position: absolute;
    left: 0;
    right: 0;
    top: 773px;
    display: flex;
    align-items: center;
    gap: 14px;
  }
  .volume-row .line {
    flex: 1;
    height: 2px;
    background: var(--rule);
  }
  .volume {
    font-size: 21px;
    font-weight: 400;
    line-height: 1;
  }
</style>
</head>
<body>
  <main class="canvas">
    <section class="label-front">
      <div class="rule-top"></div>
      <div class="brand-name">Simply Cordell</div>
      <div class="product-type">Organic Polynesian Whipped Body Butter</div>
      <div class="product-rule"></div>
      <div class="product-scent">Mango Smoothie</div>
      <div class="fruit-illustration" role="img" aria-label="Photograph of whole and diced ripe mangoes with green leaves"></div>
      <div class="volume-row">
        <span class="line"></span>
        <span class="volume">120ml</span>
        <span class="line"></span>
      </div>
    </section>
  </main>
</body>
</html>
```